Veltrane Group Business Card Design

The CEO is looking for a new trendy look for his business card.
You can stay with current branding or come up with something new/creative. It can be 3D, including Medical Office buildings. You can use our logo in a variety of colors. Please include name, title, company name, company website, email address, cell number

Target Market(s)

Real Estate Development and Construction

Industry/Entity Type

Health care real estate

Contact Information for Business Card

Rohesh Kamdar, CEO M-604.781.2249 E-roheshkamdar@veltrane.com Address:4180 Lindqvist Ave, Tampa, FL 33482 www.veltrane.com

Font styles to use
Other font styles liked:
• Be creative

Requirements
Must have
• Creative, trendy look
Nice to have
• Please go to our website to get a feel- www. veltrane.com
Should not have
• small fonts

```html
<!DOCTYPE html>
<html lang="en">
<head>
<meta charset="utf-8">
<title>Veltrane Group – Business Card</title>
<link href="https://fonts.googleapis.com/css2?family=Montserrat:wght@300;400;700;800&display=swap" rel="stylesheet">
<style>
  :root {
    --page-bg: #2a2a2a;
    --card-bg: #1e1e1e;
    --card-back-bg: #1c1c1c;
    --ink-light: #ffffff;
    --ink-soft: #d8d8d8;
    --ink-gloss: #0b0b0b;
  }
  * { margin: 0; padding: 0; box-sizing: border-box; }
  html, body {
    width: 1200px; height: 801px; overflow: hidden;
    background: var(--page-bg);
    font-family: "Montserrat", sans-serif;
  }
  .sheet {
    width: 1200px; height: 801px;
    display: flex; align-items: center; justify-content: center; gap: 28px;
  }
  .card {
    position: relative;
    width: 560px; height: 320px;
    border-radius: 22px;
    background: var(--card-bg);
    box-shadow: 0 18px 40px rgba(0,0,0,0.45);
    overflow: hidden;
  }
  .card--back { background: var(--card-back-bg); }

  /* front */
  .holder {
    position: absolute; top: 34px; right: 40px;
    display: flex; align-items: flex-start; gap: 12px; text-align: right;
  }
  .holder__name { color: var(--ink-light); font-weight: 700; font-size: 19px; letter-spacing: 0.3px; }
  .holder__title { color: var(--ink-soft); font-weight: 400; font-size: 11px; margin-top: 3px; letter-spacing: 0.5px; }
  .holder__bar { width: 16px; height: 36px; background: var(--ink-light); margin-top: -34px; }

  .wordmark {
    position: absolute; left: 40px; top: 108px;
    font-weight: 800; color: var(--ink-light);
    font-size: 52px; line-height: 1; letter-spacing: -1.5px;
  }
  .wordmark--back {
    position: static; color: var(--ink-gloss);
    font-size: 64px; letter-spacing: -2px;
  }

  .contact {
    position: absolute; left: 40px; bottom: 30px;
    color: var(--ink-soft); font-weight: 300; font-size: 12.5px; line-height: 1.55;
  }
  .contact__address { margin-bottom: 8px; }
  .contact__row { display: flex; align-items: center; gap: 9px; }
  .contact__row svg { width: 12px; height: 12px; fill: var(--ink-light); flex: none; }

  /* back */
  .card--back { display: flex; align-items: center; justify-content: center; }
</style>
</head>
<body>
<main class="sheet">
  <section class="card card--front">
    <div class="holder">
      <div>
        <div class="holder__name">Rohesh Kamdar</div>
        <div class="holder__title">CEO</div>
      </div>
    </div>
    <div class="wordmark">Veltrane Group</div>
    <div class="contact">
      <div class="contact__address">4180 Lindqvist Ave,<br>Tampa, FL 33482</div>
      <div class="contact__row">
        <svg viewBox="0 0 24 24"><path d="M6.6 10.8a15.1 15.1 0 0 0 6.6 6.6l2.2-2.2c.3-.3.7-.4 1-.2 1.1.4 2.3.6 3.6.6.6 0 1 .4 1 1V20c0 .6-.4 1-1 1A17 17 0 0 1 3 4c0-.6.4-1 1-1h3.5c.6 0 1 .4 1 1 0 1.3.2 2.5.6 3.6.1.3 0 .7-.2 1z"/></svg>
        604.781.2249
      </div>
      <div class="contact__row">
        <svg viewBox="0 0 24 24"><path d="M2 5h20v14H2z M2 5l10 8 10-8" /></svg>
        roheshkamdar@veltrane.com
      </div>
      <div class="contact__row">
        <svg viewBox="0 0 24 24"><circle cx="12" cy="12" r="10"/></svg>
        www.veltrane.com
      </div>
    </div>
  </section>

  <section class="card card--back">
    <div class="wordmark wordmark--back">Veltrane Group</div>
  </section>
</main>
</body>
</html>
```